Landscape design build company door flyer

I would like this flyer to convey a high-level of professionalism for a company that is excellent with communication with their clients as well as a company that does incredible installations

Went on vacation/holiday

```html
<!DOCTYPE html>
<html lang="en">
<head>
<meta charset="utf-8">
<title>Alder Builders – Outdoor Living Flyer</title>
<link rel="stylesheet" href="https://fonts.googleapis.com/css2?family=Montserrat:wght@300;400;600;700;800;900&family=Source+Sans+3:wght@400;600&display=swap">
<style>
  :root {
    --stage: #e8e7e4;
    --ink: #1f1f1f;
    --charcoal: #2b2b2b;
    --gold: #f6b912;
    --paper: #ffffff;
    --muted: #e6e6e6;
  }
  * { margin: 0; padding: 0; box-sizing: border-box; }
  html, body { width: 1111px; height: 1200px; overflow: hidden; background: var(--stage); }
  .spread { position: relative; width: 1111px; height: 1200px; }
  .flyer {
    position: absolute; top: 247px; width: 500px; height: 705px;
    background: var(--paper); overflow: hidden;
    box-shadow: 0 6px 18px rgba(0,0,0,0.18);
    font-family: "Montserrat", sans-serif; color: var(--ink);
  }
  .flyer--front { left: 37px; }
  .flyer--back { left: 574px; }
  .flyer__art { position: absolute; inset: 0; width: 500px; height: 705px; display: block; }
  .abs { position: absolute; }

  /* Front */
  .hero-intro { left: 23px; top: 356px; font-weight: 300; font-size: 31px; line-height: 33px; }
  .hero-title { left: 23px; top: 426px; font-weight: 900; font-size: 40px; line-height: 40px; }
  .hero-accent { left: 23px; top: 503px; font-weight: 800; font-size: 29px; color: var(--gold); }
  .hero-lead { left: 23px; top: 552px; width: 228px; font-weight: 700; font-size: 14.5px; line-height: 20px; }
  .hero-note { left: 23px; top: 643px; width: 250px; font-family: "Source Sans 3", sans-serif; font-size: 10.5px; line-height: 14px; }
  .services { left: 326px; top: 342px; color: var(--paper); }
  .services__title { font-weight: 900; font-size: 26px; line-height: 22px; color: var(--gold); }
  .services__sub { font-weight: 900; font-size: 17px; line-height: 17px; color: var(--gold); }
  .services__list { list-style: none; margin-top: 3px; font-family: "Source Sans 3", sans-serif; font-size: 10.5px; }
  .services__list li { height: 17.2px; line-height: 17.2px; padding-left: 18px; position: relative; }
  .services__list li::before {
    content: ""; position: absolute; left: 1px; top: 4px;
    border-left: 5px solid transparent; border-right: 5px solid transparent;
    border-bottom: 9px solid var(--gold);
  }

  /* Back */
  .why-title { left: 14px; top: 52px; font-weight: 900; font-size: 19px; line-height: 22px; }
  .why-title span { color: var(--gold); }
  .why-list { left: 14px; top: 156px; list-style: none; font-weight: 600; font-size: 10.4px; line-height: 13px; }
  .why-list li { margin-bottom: 8.5px; }
  .brand { left: 0; width: 500px; top: 592px; text-align: center; }
  .brand__name { display: inline-flex; align-items: center; gap: 8px; font-weight: 700; font-size: 19px; color: var(--paper); letter-spacing: 0.5px; }
  .brand__mark { width: 10px; height: 10px; background: var(--paper); display: inline-block; }
  .brand__address { left: 0; width: 500px; top: 632px; text-align: center; font-family: "Source Sans 3", sans-serif; font-size: 10px; color: var(--gold); }
  .contact { left: 14px; top: 656px; font-weight: 700; font-size: 15px; line-height: 21px; }
  .contact__row { display: flex; align-items: center; gap: 5px; }
  .contact__row--small { font-size: 12.5px; }
  .contact__icon { width: 12px; height: 12px; }
  .web { left: 274px; top: 668px; display: flex; align-items: center; gap: 6px; font-weight: 700; font-size: 15px; color: var(--paper); }
</style>
</head>
<body>
<main class="spread">

  <!-- Front side -->
  <section class="flyer flyer--front">
    <svg class="flyer__art" viewBox="0 0 500 705">
      <defs>
        <linearGradient id="pavilionTone" x1="0" y1="0" x2="1" y2="1">
          <stop offset="0" stop-color="#8fb0c8"/><stop offset="0.35" stop-color="#6c7a55"/>
          <stop offset="0.7" stop-color="#5b4a3a"/><stop offset="1" stop-color="#4a4a4c"/>
        </linearGradient>
        <linearGradient id="firepitTone" x1="0" y1="0" x2="1" y2="1">
          <stop offset="0" stop-color="#6a5a4a"/><stop offset="1" stop-color="#2e2c2a"/>
        </linearGradient>
        <linearGradient id="poolTone" x1="0" y1="0" x2="0" y2="1">
          <stop offset="0" stop-color="#e2e0da"/><stop offset="0.5" stop-color="#7fc8cf"/><stop offset="1" stop-color="#2aa0b0"/>
        </linearGradient>
        <linearGradient id="deckTone" x1="0" y1="0" x2="1" y2="1">
          <stop offset="0" stop-color="#6f8a5a"/><stop offset="0.5" stop-color="#b67a3e"/><stop offset="1" stop-color="#7a4a22"/>
        </linearGradient>
      </defs>
      <polygon points="0,0 500,0 500,8 210,331 0,331" fill="url(#pavilionTone)" role="img" aria-label="Photo of a covered outdoor pavilion with stone fireplace and timber roof"/>
      <polygon points="0,331 210,331 500,8 500,22 216,341 0,341" fill="var(--gold)"/>
      <polygon points="500,30 500,705 276,705 276,378" fill="var(--charcoal)"/>
      <g transform="translate(438 89) rotate(45)">
        <rect x="-50" y="-50" width="100" height="100" fill="var(--paper)"/>
        <rect x="-46" y="-46" width="92" height="92" fill="url(#firepitTone)" role="img" aria-label="Photo of an evening fire pit lounge"/>
      </g>
      <g transform="translate(360 210) rotate(45)">
        <rect x="-50" y="-50" width="100" height="100" fill="var(--paper)"/>
        <rect x="-46" y="-46" width="92" height="92" fill="url(#poolTone)" role="img" aria-label="Photo of a modern home with a turquoise pool"/>
      </g>
      <g transform="translate(280 300) rotate(45)">
        <rect x="-50" y="-50" width="100" height="100" fill="var(--paper)"/>
        <rect x="-46" y="-46" width="92" height="92" fill="url(#deckTone)" role="img" aria-label="Photo of a wooden deck in a garden"/>
      </g>
    </svg>

    <p class="abs hero-intro">Let’s<br>Create Your</p>
    <h1 class="abs hero-title">Dream<br>Outdoor</h1>
    <p class="abs hero-accent">Living Space!</p>
    <p class="abs hero-lead">Discover the endless possibilities for your outdoor space with The Alder Builders Team.</p>
    <p class="abs hero-note">Our team of skilled artisans is dedicated to turning your outdoor space into a breathtaking oasis that you’ll love coming home to.</p>

    <div class="abs services">
      <h2 class="services__title">Services</h2>
      <p class="services__sub">we provide:</p>
      <ul class="services__list">
        <li>Landscape design</li><li>Landscaping</li><li>Hardscaping</li>
        <li>Retaining wall design</li><li>Retaining walls</li><li>Pool designs</li>
        <li>Driveways</li><li>Firepits</li><li>Pavers</li><li>Deck designs</li>
        <li>Luxury outdoor elements</li><li>Outdoor living spaces</li><li>Patio designs</li>
        <li>Outdoor lighting</li><li>Outdoor kitchen spaces</li><li>Fencing</li>
        <li>Fireplaces</li><li>Sheds</li>
      </ul>
    </div>
  </section>

  <!-- Back side -->
  <section class="flyer flyer--back">
    <svg class="flyer__art" viewBox="0 0 500 705">
      <defs>
        <linearGradient id="gazeboTone" x1="0" y1="0" x2="1" y2="1">
          <stop offset="0" stop-color="#5e7d3a"/><stop offset="0.45" stop-color="#6e5e4c"/>
          <stop offset="0.8" stop-color="#7d8a96"/><stop offset="1" stop-color="#5a5c60"/>
        </linearGradient>
        <linearGradient id="plungeTone" x1="0" y1="0" x2="1" y2="1">
          <stop offset="0" stop-color="#9aa2a8"/><stop offset="0.5" stop-color="#3fb6c8"/><stop offset="1" stop-color="#8a9096"/>
        </linearGradient>
        <linearGradient id="hearthTone" x1="0" y1="0" x2="0" y2="1">
          <stop offset="0" stop-color="#8e8c88"/><stop offset="0.6" stop-color="#a58a6a"/><stop offset="1" stop-color="#6d6a66"/>
        </linearGradient>
        <linearGradient id="pondTone" x1="0" y1="0" x2="0" y2="1">
          <stop offset="0" stop-color="#a89a88"/><stop offset="0.5" stop-color="#6a7276"/><stop offset="1" stop-color="#9a6a3a"/>
        </linearGradient>
      </defs>
      <polygon points="85,0 500,0 500,400 290,400" fill="url(#gazeboTone)" role="img" aria-label="Photo of a curtained gazebo with lounge seating in a terraced garden"/>
      <polygon points="72,0 85,0 290,400 277,400" fill="var(--gold)"/>
      <polygon points="0,497 140,410 228,369 368,403 500,403 500,650 0,650" fill="var(--charcoal)"/>
      <rect x="360" y="396" width="140" height="7" fill="var(--gold)"/>
      <g transform="translate(228 369) rotate(45)">
        <rect x="-63" y="-63" width="126" height="126" fill="var(--paper)"/>
        <rect x="-59" y="-59" width="118" height="118" fill="url(#plungeTone)" role="img" aria-label="Photo of a plunge pool from above"/>
      </g>
      <g transform="translate(132 497) rotate(45)">
        <rect x="-63" y="-63" width="126" height="126" fill="var(--paper)"/>
        <rect x="-59" y="-59" width="118" height="118" fill="url(#hearthTone)" role="img" aria-label="Photo of an outdoor stone fireplace"/>
      </g>
      <g transform="translate(368 488) rotate(45)">
        <rect x="-63" y="-63" width="126" height="126" fill="var(--paper)"/>
        <rect x="-59" y="-59" width="118" height="118" fill="url(#pondTone)" role="img" aria-label="Photo of a stone water feature and deck"/>
      </g>
      <rect x="0" y="650" width="500" height="55" fill="var(--paper)"/>
      <polygon points="242,650 500,650 500,705 262,705" fill="var(--gold)"/>
    </svg>

    <h2 class="abs why-title">Why<br>Choose<br><span>Alder<br>Builders?</span></h2>
    <ul class="abs why-list">
      <li>20-year track<br>record serving<br>Greater Seattle</li>
      <li>Uncompromising quality<br>– Every project. Every day</li>
      <li>Veteran owned and operated</li>
      <li>Personal service and<br>proactive communication</li>
      <li>Clean cut, professional,<br>and highly skilled installers</li>
      <li>Fair, upfront estimates<br>with no hidden fees</li>
      <li>Sustainable materials<br>and construction<br>techniques</li>
    </ul>

    <div class="abs brand"><span class="brand__name"><i class="brand__mark"></i>ALDER BUILDERS</span></div>
    <p class="abs brand__address">1180 Fernwood Ave, Redmond, WA 98052</p>

    <div class="abs contact">
      <div class="contact__row">
        <svg class="contact__icon" viewBox="0 0 24 24" fill="none" stroke="currentColor" stroke-width="2.2"><path d="M5 3h4l2 5-2.5 1.5a11 11 0 0 0 6 6L16 13l5 2v4a2 2 0 0 1-2 2A17 17 0 0 1 3 5a2 2 0 0 1 2-2z"/></svg>
        (206) 555-0148
      </div>
      <div class="contact__row contact__row--small">
        <svg class="contact__icon" viewBox="0 0 24 24" fill="none" stroke="currentColor" stroke-width="2.2"><rect x="3" y="6" width="18" height="13" rx="1"/><path d="M3 7l9 7 9-7"/></svg>
        info@alderbuilders.com
      </div>
    </div>
    <div class="abs web">
      <svg class="contact__icon" viewBox="0 0 24 24" fill="none" stroke="currentColor" stroke-width="2"><circle cx="12" cy="12" r="9"/><path d="M3 12h18M12 3c3 3 3 15 0 18M12 3c-3 3-3 15 0 18"/></svg>
      alderbuilders.com
    </div>
  </section>

</main>
</body>
</html>
```